Lanternfield Drinks business cards

We need a business card design for our new logo. The company is modern, progressive, professional, yet approachable. The key products are ready to drink bottles and cans of coffee based beverages.
These cards will be a critical part of the first impression made by our sales organization, business development team, and all external facing personnel.
Card can be a vertical or horizontal orientation.

Target Market(s)

Customers, suppliers, business partners

Industry/Entity Type

Business

Contact Information for Business Card

Business cards should feature Company Name and Logo.

Font styles to use
Serif

Colors

Designer to choose colors to be used in the design.

Requirements
Must have
• Strong readability of Name, phone #, mobile number and email address.
• Job title, website url, Street Address, and other details can be secondary level readability.
Nice to have
• High impact, simplistic quality design.
• Ok to utilize the 'H in the box' separate from the company name

```html
<!DOCTYPE html>
<html lang="en">
<head>
<meta charset="utf-8">
<title>Lanternfield Drinks – Business Cards</title>
<link rel="stylesheet" href="https://fonts.googleapis.com/css2?family=Crimson+Pro:ital,wght@0,400;0,600;0,700;1,400&display=swap">
<style>
  :root {
    --bg: #b9b9b9;
    --orange-top: #e0802f;
    --orange-bottom: #c0482a;
    --brand-red: #cf4e2a;
    --band-amber: #dd8a2e;
    --paper: #f2f2f2;
    --ink: #222222;
    --white: #ffffff;
  }
  * { box-sizing: border-box; margin: 0; padding: 0; }
  html, body {
    width: 1200px; height: 576px; overflow: hidden;
    background: var(--bg);
    font-family: "Crimson Pro", Georgia, serif;
  }
  .stage { position: relative; width: 1200px; height: 576px; }

  .card {
    position: absolute; top: 138px;
    width: 485px; height: 294px;
    border-radius: 12px; overflow: hidden;
    box-shadow: 0 3px 6px rgba(0,0,0,0.25);
  }

  /* Front */
  .card-front {
    left: 82px;
    background: linear-gradient(180deg, var(--orange-top) 0%, #d86a2c 55%, var(--orange-bottom) 100%);
    display: flex; flex-direction: column; align-items: center;
  }
  .card-front .brand-square {
    margin-top: 78px;
    width: 76px; height: 76px;
    border: 3px solid var(--white);
  }
  .card-front .brand-name {
    margin-top: 18px;
    color: var(--white);
    font-weight: 700; font-size: 34px; letter-spacing: 1px;
    text-transform: uppercase;
  }

  /* Back */
  .card-back { left: 602px; background: var(--paper); }
  .card-back .brand {
    position: absolute; left: 30px; top: 82px; width: 200px;
    display: flex; flex-direction: column; align-items: center;
  }
  .card-back .brand-square {
    width: 58px; height: 58px;
    border: 3px solid var(--brand-red);
  }
  .card-back .brand-name {
    margin-top: 12px;
    color: var(--brand-red);
    font-weight: 700; font-size: 22px; letter-spacing: 0.5px;
    text-transform: uppercase; white-space: nowrap;
  }

  .contact { position: absolute; left: 270px; top: 58px; color: var(--ink); }
  .contact .person-name { color: var(--brand-red); font-weight: 600; font-size: 20px; line-height: 1.1; }
  .contact .job-title { font-style: italic; font-size: 13px; margin-top: 2px; }
  .contact .lines { margin-top: 22px; list-style: none; }
  .contact .lines li {
    display: flex; align-items: center; gap: 10px;
    font-size: 14px; line-height: 17.5px;
  }
  .contact .lines svg { width: 11px; height: 11px; fill: var(--brand-red); flex: none; }
  .contact .address { margin-top: 4px; font-size: 14px; line-height: 17px; }

  .strip-amber {
    position: absolute; left: 0; bottom: 0; width: 240px; height: 10px;
    background: var(--band-amber);
  }
  .band-web {
    position: absolute; right: 0; bottom: 0; width: 260px; height: 37px;
  }
  .band-web svg { position: absolute; inset: 0; }
  .band-web .web {
    position: absolute; left: 48px; top: 9px;
    color: var(--white); font-size: 13px;
  }
</style>
</head>
<body>
<div class="stage">

  <section class="card card-front">
    <div class="brand-square"></div>
    <div class="brand-name">Lanternfield Drinks</div>
  </section>

  <section class="card card-back">
    <div class="brand">
      <div class="brand-square"></div>
      <div class="brand-name">Lanternfield Drinks</div>
    </div>

    <div class="contact">
      <div class="person-name">Alex Marlow Reed</div>
      <div class="job-title">Managing Director</div>
      <ul class="lines">
        <li>
          <svg viewBox="0 0 12 12"><path d="M1 4c0-2 2-3 5-3s5 1 5 3v1H8V4H4v1H1zM2 6h8l1 5H1z"/></svg>
          555.210.4408
        </li>
        <li>
          <svg viewBox="0 0 12 12"><path d="M3 0h6a1 1 0 0 1 1 1v10a1 1 0 0 1-1 1H3a1 1 0 0 1-1-1V1a1 1 0 0 1 1-1zm0 2v7h6V2z"/></svg>
          555.318.9062
        </li>
        <li>
          <svg viewBox="0 0 12 12"><path d="M0 2h12v8H0zM1 3l5 4 5-4z"/></svg>
          alex@lanternfield.com
        </li>
      </ul>
      <div class="address">48 Kiln Row,<br>Brookmere, US 204718</div>
    </div>

    <div class="strip-amber"></div>
    <div class="band-web">
      <svg viewBox="0 0 260 37" preserveAspectRatio="none">
        <path d="M20 0H260V37H0L14 5Q16 0 20 0z" fill="var(--brand-red)"/>
      </svg>
      <span class="web">www.lanternfield.com</span>
    </div>
  </section>

</div>
</body>
</html>
```